Sunset Harbor Living Web Page

We need a web page design that has two intro pages - first being a 'home page', then a link to the second page that has the 'content tabs' and a 'call to action' (see below).

The business helps people that wish to retire to S.E.Asia (Thailand, Malaysia, Indonesia,The Philippines etc) - to enjoy the lifestyle and the remaining years of their lives. What attracts S.E.Asia to many people is the lower cost, the atmoshpere and beauty of the tropics and the vibrancy of the various countries.

People that are wishing to make the most of their retirement and are adventurous at a great bargain compared to the cost of their own countries will be interested.

We help them achieve this - visa, financials (tax, gov't payments etc), introduce them to the right people for property, clubs, retirement facilities, insurance and so forth.

Therefore we are providing an extremely wide ranging service and this site will provide broad but general information only - with a call to action to come and see us for more specific information and how we can help them specifically.

This site will be predominantly for travel and lifestyle, it will be linked with another financial services (financial planning) site later down the track.

The colour scheme is dark green and blue - as per the attached logo design. Photos and background just think lifestyle and S.E.Asia - beaches/mountains/water/recreational activities for retirees.

Target market is mostly those coming up to retirement to those that are already retired. But we also expect to have some interest with younger people that would like to find out more and plan for the future. So a broad age group but I would say mostly 40-70 yrs old.

On the first (Home) page we would like our company name 'Sunset Harbor Living', our logo (which will be on all pages) and a statement such as: “Imagine a retirement where your dreams are brought to life, and you have never felt more alive. Let us show you how”. Then a link to the second page.

We would like an uncluttered site. On the second (contents) page the tabs would be:

- Visa
- Property
- Financials
- Travel
- Insurance & Healthcare
- Medical Tourism
- Cost of living
- Weekly Blogs and articles
- Sunset Harbor Living story

We would also like a call to action on the second page - asking them to leave their contact details if they wish to learn more or sign up to our weekly newsletter/blog.

We are open to suggestions and your imaginations.

Thank you
Malcolm

Font styles to use
Serif
Script

Colors
0255a3
3377b5
00a990
9bcb3c
abd036
33b8a4
85abd2
cadf82
86cfc6

Requirements
Must have
• I have been asked by the web designer to receive a 'Web Font' so that we can 'get off of Zentrofy'. Hope that makes sense.

```html
<!DOCTYPE html>
<html lang="en">
<head>
<meta charset="utf-8">
<title>Sunset Harbor Living</title>
<link href="https://fonts.googleapis.com/css2?family=Open+Sans:wght@300;400;600;700&display=swap" rel="stylesheet">
<style>
:root{
  --green:#0aa64e;
  --green-dark:#078a3f;
  --green-title:#17a55a;
  --blue:#1593d3;
  --blue-text:#1c8ccd;
  --grey-text:#777;
  --body-text:#333;
  --footer:#262626;
  --footer-bottom:#1b1b1b;
  --white:#fff;
}
*{box-sizing:border-box;margin:0;padding:0}
html,body{width:1200px;height:2655px;overflow:hidden}
body{font-family:"Open Sans",Arial,sans-serif;color:var(--body-text);background:var(--white);position:relative}
.wrap{width:934px;margin:0 auto;position:relative}

/* header */
.site-header{height:138px;position:relative}
.brand{position:absolute;left:133px;top:38px;display:flex;align-items:center;gap:10px}
.brand-mark{width:44px;height:44px;border-radius:50%;background:var(--green)}
.brand-name{font-size:24px;font-weight:700;color:var(--blue-text)}
.social{position:absolute;left:610px;top:27px;display:flex;gap:8px}
.social span{width:25px;height:25px;border-radius:50%;background:#b9bdc2}
.social span:first-child{background:#3b5998}
.search{position:absolute;left:850px;top:22px;width:216px;height:36px;border:1px solid #ddd;display:flex;align-items:center;justify-content:space-between;padding:0 12px;font-size:11px;color:#555}
.contact-item{position:absolute;top:82px;display:flex;align-items:center;gap:8px}
.contact-item .label{text-align:right;font-size:11px;color:#555;line-height:1.2}
.contact-item .label strong{display:block;font-weight:400;font-size:18px;color:var(--blue-text)}
.contact-item .ring{width:30px;height:30px;border:1px solid #ccc;border-radius:50%;display:flex;align-items:center;justify-content:center}
.call{right:134px;left:auto}
.call{left:672px}
.mail{left:850px}

/* nav */
.main-nav{height:39px;background:var(--green)}
.main-nav ul{list-style:none;display:flex;height:39px;width:934px;margin:0 auto}
.main-nav li{color:var(--white);font-size:11.3px;font-weight:600;padding:0 10.6px;line-height:39px;white-space:nowrap}
.main-nav li.active{background:var(--green-dark)}

/* hero */
.hero{height:435px;position:relative;background:linear-gradient(180deg,#d9a05a 0%,#f2b85a 25%,#e58a34 42%,#5b7b8e 52%,#2c5a78 70%,#a97848 86%,#6b4a2a 100%)}
.hero-arrow{position:absolute;top:205px;width:22px;height:30px;background:rgba(0,0,0,.35);display:flex;align-items:center;justify-content:center}
.hero-arrow.left{left:0}.hero-arrow.right{right:0}

/* newsletter */
.newsletter{height:64px;background:var(--blue);display:flex;align-items:center;padding-left:190px}
.newsletter h2{color:var(--white);font-size:24px;font-weight:700;display:flex;align-items:center;gap:10px;width:396px}
.field{height:30px;background:var(--white);font-size:10.5px;color:#666;padding:0 12px;display:flex;align-items:center}
.newsletter .field{width:166px;margin-right:13px}
.btn-dark{height:30px;padding:0 11px;background:#333;color:#ddd;font-size:11px;display:flex;align-items:center;letter-spacing:.5px}

/* welcome */
.welcome{height:275px;text-align:center;padding-top:50px}
.welcome h1{font-weight:400;font-size:32px;color:var(--green-title);line-height:40px}
.welcome p{font-size:12.2px;line-height:20px;color:var(--grey-text);margin-top:10px}
.btn-light{display:inline-block;margin-top:17px;background:#e3e3e3;color:#777;font-size:12px;padding:8px 15px}

/* services */
.services{height:1017px;background:linear-gradient(180deg,#0da24e 0%,#0b9b48 45%,#108a45 80%,#0b7b3b 100%);padding-top:32px}
.services h2{text-align:center;color:var(--white);font-weight:300;font-size:32px;line-height:44px}
.service-grid{display:grid;grid-template-columns:repeat(3,287px);column-gap:36px;row-gap:37px;margin-top:30px;justify-content:start}
.service{text-align:center;color:var(--white);height:262px}
.service .photo{height:173px}
.service h3{font-weight:400;font-size:19px;margin-top:12px;line-height:24px}
.service p{font-size:10.2px;line-height:15px;color:#d6efdf;margin-top:3px;padding:0 2px}
.service.center{grid-column:2}

/* blog */
.blog{height:390px;padding-top:40px}
.blog-head{display:flex;justify-content:space-between;align-items:center}
.blog-head h2{font-weight:400;font-size:26px;color:var(--blue-text)}
.pager{display:flex;gap:3px}
.pager span{width:18px;height:18px;border:1px solid #ccc;border-radius:50%;display:flex;align-items:center;justify-content:center}
.posts{display:grid;grid-template-columns:repeat(3,280px);column-gap:47px;margin-top:12px}
.post .photo{height:151px}
.post h3{font-weight:400;font-size:13.5px;line-height:19px;color:#222;margin-top:22px}
.post p{font-size:10px;line-height:14.5px;color:#999;margin-top:9px}

/* footer */
.site-footer{height:239px;background:var(--footer);padding-top:24px}
.footer-cols{display:flex}
.footer-col h4{font-weight:400;font-size:18px;color:var(--green-title);line-height:22px}
.col-form{width:311px;border-right:1px solid #444;height:190px}
.col-links{width:294px;padding-left:20px;border-right:1px solid #444;height:190px}
.col-info{padding-left:16px;flex:1}
.form-row{display:flex;gap:13px;margin-top:11px}
.form-row .field{width:141px;height:30px;font-size:10px}
.form-row .field.wide{width:294px}
.submit{margin-top:9px;width:62px;height:30px;background:#111;color:#eee;font-size:10px;display:flex;align-items:center;justify-content:center}
.links{display:grid;grid-template-columns:138px 150px;margin-top:6px}
.links ul{list-style:none}
.links li{font-size:10px;color:#aaa;line-height:25.5px}
.links li::before{content:"• "}
.info{font-size:10px;color:#ccc;line-height:26px;margin-top:6px}
.map{margin-top:8px;width:308px;height:90px;background:linear-gradient(135deg,#e8e8e8,#d6dbe0)}
.site-bottom{height:58px;background:var(--footer-bottom);color:#ddd;font-size:10px;text-align:center;line-height:58px}
</style>
</head>
<body>

<header class="site-header">
  <div class="brand"><span class="brand-mark"></span><span class="brand-name">Sunset Harbor Living</span></div>
  <div class="social" aria-label="Social links"><span></span><span></span><span></span><span></span><span></span><span></span><span></span></div>
  <div class="search">Search
    <svg width="12" height="12" viewBox="0 0 12 12"><circle cx="5" cy="5" r="3.8" fill="none" stroke="#0aa64e" stroke-width="1.6"/><line x1="8" y1="8" x2="11" y2="11" stroke="#0aa64e" stroke-width="1.8"/></svg>
  </div>
  <div class="contact-item call">
    <div class="label">Call us on<strong>555 010 6548</strong></div>
    <span class="ring"><svg width="12" height="12" viewBox="0 0 12 12"><path d="M2 1l2 0 1 3-1.5 1a6 6 0 0 0 3.5 3.5L8 7l3 1v2c0 1-1 1-1 1A9 9 0 0 1 1 2s0-1 1-1z" fill="#999"/></svg></span>
  </div>
  <div class="contact-item mail">
    <div class="label">Email<strong>info@sunsetharborliving.com</strong></div>
    <span class="ring"><svg width="12" height="10" viewBox="0 0 12 10"><rect x="0.5" y="0.5" width="11" height="9" fill="#999"/><path d="M1 1l5 4 5-4" stroke="#fff" fill="none"/></svg></span>
  </div>
</header>

<nav class="main-nav">
  <ul>
    <li class="active">Home</li><li>Visa</li><li>Property</li><li>Financials</li><li>Travel</li><li>Insurance &amp; Healthcare</li><li>Medical Tourism</li><li>Cost of living</li><li>Weekly Blogs and articles</li><li>Sunset Harbor Living story</li><li>Contact us</li>
  </ul>
</nav>

<section class="hero" role="img" aria-label="Retired couple relaxing in beach chairs facing a tropical sunset over the sea">
  <span class="hero-arrow left"><svg width="8" height="12" viewBox="0 0 8 12"><path d="M7 1L2 6l5 5" stroke="#fff" stroke-width="1.5" fill="none"/></svg></span>
  <span class="hero-arrow right"><svg width="8" height="12" viewBox="0 0 8 12"><path d="M1 1l5 5-5 5" stroke="#fff" stroke-width="1.5" fill="none"/></svg></span>
</section>

<section class="newsletter">
  <h2><svg width="22" height="18" viewBox="0 0 22 18"><rect x="1" y="1" width="20" height="16" rx="2" fill="none" stroke="#fff" stroke-width="2"/><path d="M2 3l9 7 9-7" stroke="#fff" stroke-width="2" fill="none"/></svg>Weekly Newsletter Subscribe</h2>
  <div class="field">Name</div>
  <div class="field">Email</div>
  <div class="btn-dark">SIGN UP</div>
</section>

<section class="welcome">
  <div class="wrap">
    <h1>Welcome to Sunset Harbor Living</h1>
    <p>Phasellus arcu nulla, vulputate in vestibulum a, sagittis malesuada nunc. Donec finibus diam sit amet porta bibendum. In hac habitasse platea dictumst. Vivamus ultricies non magna vitae feugiat. Ut volutpat porttitor vulputate. Integer dictum egestas dolor, vitae sodales ex tempus ut. Etiam vitae tincidunt metus. Praesent in vulputate sapien. Quisque facilisis orci ipsum, mattis facilisis leo elementum sed. Nullam ut erat ullamcorper, tristique lacus eget, imperdiet libero. Class aptent taciti sociosqu ad litora torquent per conubia nostra, per inceptos himenaeos. Aliquam a blandit mauris. Nullam metus ipsum, varius ut nulla id, luctus rhoncus diam.</p>
    <span class="btn-light">Read more</span>
  </div>
</section>

<section class="services" aria-label="Our Services">
  <div class="wrap">
    <h2>Our Services</h2>
    <div class="service-grid">
      <article class="service"><div class="photo" role="img" aria-label="Passport pages with a rubber visa stamp" style="background:linear-gradient(135deg,#e9e4d6,#c9c2b0)"></div><h3>Visa</h3><p>Praesent in vulputate sapien. Quisque facilisis orci ipsum, mattis facilisis leo elementum sed. Nullam ut erat ullamcorper, tristique lacus eget, imperdiet libero.</p></article>
      <article class="service"><div class="photo" role="img" aria-label="Coffee cup on a wooden table overlooking green tea hills" style="background:linear-gradient(180deg,#b8c9c8,#6e9a4a 45%,#4c3a2c)"></div><h3>Property</h3><p>Praesent in vulputate sapien. Quisque facilisis orci ipsum, mattis facilisis leo elementum sed. Nullam ut erat ullamcorper, tristique lacus eget, imperdiet libero.</p></article>
      <article class="service"><div class="photo" role="img" aria-label="Small globe resting on scattered banknotes" style="background:linear-gradient(135deg,#d8cba8,#b2a98a)"></div><h3>Financials</h3><p>Praesent in vulputate sapien. Quisque facilisis orci ipsum, mattis facilisis leo elementum sed. Nullam ut erat ullamcorper, tristique lacus eget, imperdiet libero.</p></article>
      <article class="service"><div class="photo" role="img" aria-label="Hands over a travel map with coffee and a watch" style="background:linear-gradient(135deg,#8a7d70,#cfc6b2)"></div><h3>Travel</h3><p>Praesent in vulputate sapien. Quisque facilisis orci ipsum, mattis facilisis leo elementum sed. Nullam ut erat ullamcorper, tristique lacus eget, imperdiet libero.</p></article>
      <article class="service"><div class="photo" role="img" aria-label="Health insurance paperwork with a stethoscope and banknotes" style="background:linear-gradient(135deg,#e6e6e6,#9aa3a0)"></div><h3>Insurance &amp; Healthcare</h3><p>Praesent in vulputate sapien. Quisque facilisis orci ipsum, mattis facilisis leo elementum sed. Nullam ut erat ullamcorper, tristique lacus eget, imperdiet libero.</p></article>
      <article class="service"><div class="photo" role="img" aria-label="Doctor in a white coat with an airplane in the sky behind" style="background:linear-gradient(180deg,#c7d6e6,#eef2f6)"></div><h3>Medical Tourism</h3><p>Praesent in vulputate sapien. Quisque facilisis orci ipsum, mattis facilisis leo elementum sed. Nullam ut erat ullamcorper, tristique lacus eget, imperdiet libero.</p></article>
      <article class="service center"><div class="photo" role="img" aria-label="Receipt titled cost of living beside a few coins" style="background:linear-gradient(135deg,#b9a58c,#ece8e0)"></div><h3>Cost of living</h3><p>Praesent in vulputate sapien. Quisque facilisis orci ipsum, mattis facilisis leo elementum sed. Nullam ut erat ullamcorper, tristique lacus eget, imperdiet libero.</p></article>
    </div>
  </div>
</section>

<section class="blog">
  <div class="wrap">
    <div class="blog-head">
      <h2>Blog</h2>
      <div class="pager">
        <span><svg width="6" height="8" viewBox="0 0 6 8"><path d="M5 1L2 4l3 3" stroke="#999" fill="none"/></svg></span>
        <span><svg width="6" height="8" viewBox="0 0 6 8"><path d="M1 1l3 3-3 3" stroke="#999" fill="none"/></svg></span>
      </div>
    </div>
    <div class="posts">
      <article class="post"><div class="photo" role="img" aria-label="City skyline with twin towers lit at night" style="background:linear-gradient(180deg,#0c2a6b,#1f5fb8 60%,#0b1f44)"></div><h3>Maecenas porta, nisl consequat pharetra, arcu dui rutrum leo, id faucibus tellus orci vel augue.</h3><p>Integer lacinia fermentum odio quis facilisis. Pellentesque pellentesque risus felis, in vehicula quam eleifend quis. Integer quam sem, bibendum eu pharetra eget, vehicula non.</p></article>
      <article class="post"><div class="photo" role="img" aria-label="Misty mountains above green tea plantation terraces" style="background:linear-gradient(180deg,#7d8a9c,#9aa79a 40%,#3f7a2e)"></div><h3>Maecenas porta, nisl consequat pharetra, arcu dui rutrum leo, id faucibus tellus orci vel augue.</h3><p>Integer lacinia fermentum odio quis facilisis. Pellentesque pellentesque risus felis, in vehicula quam eleifend quis. Integer quam sem, bibendum eu pharetra eget, vehicula non.</p></article>
      <article class="post"><div class="photo" role="img" aria-label="Rolling green tea fields under a cloudy sky" style="background:linear-gradient(180deg,#9fb0c0,#5c9a3a 45%,#2f6b1f)"></div><h3>Maecenas porta, nisl consequat pharetra, arcu dui rutrum leo, id faucibus tellus orci vel augue.</h3><p>Integer lacinia fermentum odio quis facilisis. Pellentesque pellentesque risus felis, in vehicula quam eleifend quis. Integer quam sem, bibendum eu pharetra eget, vehicula non.</p></article>
    </div>
  </div>
</section>

<footer class="site-footer">
  <div class="wrap footer-cols">
    <div class="footer-col col-form">
      <h4>Contact us</h4>
      <div class="form-row"><div class="field">Name</div><div class="field">Email</div></div>
      <div class="form-row"><div class="field">Phone</div><div class="field">City</div></div>
      <div class="form-row"><div class="field wide">Message</div></div>
      <div class="submit">SUBMIT</div>
    </div>
    <div class="footer-col col-links">
      <h4>Links</h4>
      <div class="links">
        <ul><li>Home</li><li>Visa</li><li>Property</li><li>Financials</li><li>Travel</li><li>Insurance &amp; Healthcare</li></ul>
        <ul><li>Medical Tourism</li><li>Cost of living</li><li>Weekly Blogs and articles</li><li>Sunset Harbor Living story</li><li>Contact us</li></ul>
      </div>
    </div>
    <div class="footer-col col-info">
      <h4>Contact Info</h4>
      <div class="info">• 24 Building name, Street name, City - Zipcode<br>• Phone : 555 010 6549 &nbsp;&nbsp;• Email: info@sunsetharborliving.com</div>
      <div class="map" role="img" aria-label="Street map showing the office location"></div>
    </div>
  </div>
</footer>
<div class="site-bottom">Copyright © 2016 Sunset Harbor Living. All rights reserved</div>

</body>
</html>
```